Executive Business Card for Healthcare Company [Need Today]

I need a business card design for a healthcare company. The only branding the company has thus far is a logo. The cards will be utilized by company executives. The design I envision will be vibrant and appealing but with a corporate feel. They shouldn't be too casual or playful. I would like to complete this project TODAY if possible.

Target Market(s)

Healthcare vendors, other executives in healthcare and pharmaceuticals

Industry/Entity Type

Pharmaceutical

Contact Information for Business Card

See attachment

Font styles to use
Serif
Sans Serif

Colors

Designer to choose colors to be used in the design.

```html
<!DOCTYPE html>
<html lang="en">
<head>
<meta charset="UTF-8">
<title>Meriden Therapeutics – Business Card</title>
<link href="https://fonts.googleapis.com/css2?family=Roboto:wght@300;400&display=swap" rel="stylesheet">
<style>
  :root {
    --bg: #e8e9eb;
    --card: #ffffff;
    --teal: #1ea8b8;
    --green: #4cb08a;
    --ink: #555a5e;
    --muted: #8a9095;
    --white: #ffffff;
  }
  * { margin: 0; padding: 0; box-sizing: border-box; }
  html, body { width: 1200px; height: 726px; overflow: hidden; }
  body {
    background: var(--bg);
    font-family: "Roboto", Arial, sans-serif;
    position: relative;
  }
  .card {
    position: absolute;
    top: 208px;
    width: 540px;
    height: 309px;
    background: var(--card);
    box-shadow: 0 6px 18px rgba(0,0,0,0.12);
    overflow: hidden;
  }
  .card--front { left: 40px; }
  .card--back { left: 620px; }

  /* Front */
  .front-brand {
    position: absolute;
    top: 96px;
    left: 0;
    width: 100%;
    display: flex;
    align-items: center;
    justify-content: center;
    gap: 18px;
  }
  .brand-dot {
    width: 74px;
    height: 74px;
    border-radius: 50%;
    border: 3px solid var(--green);
  }
  .brand-name {
    font-weight: 300;
    color: var(--teal);
    font-size: 34px;
    line-height: 1.1;
    letter-spacing: 0.5px;
  }
  .front-web {
    position: absolute;
    bottom: 62px;
    width: 100%;
    text-align: center;
    font-size: 14px;
    letter-spacing: 4px;
    color: var(--ink);
  }
  .front-web span { color: var(--teal); }

  /* Back */
  .back-brand {
    position: absolute;
    top: 48px;
    left: 34px;
    font-weight: 300;
    color: var(--teal);
    font-size: 30px;
    letter-spacing: 0.5px;
  }
  .band {
    position: absolute;
    top: 96px;
    left: 0;
    width: 100%;
    height: 158px;
    background: linear-gradient(110deg, var(--teal) 0%, var(--green) 100%);
  }
  .band-mark {
    position: absolute;
    top: 58px;
    right: 40px;
    width: 138px;
    height: 138px;
    border-radius: 50%;
    background: var(--white);
    border: 5px solid var(--green);
  }
  .contact {
    position: absolute;
    top: 114px;
    left: 34px;
    color: var(--white);
  }
  .contact-name { font-size: 22px; font-weight: 400; }
  .contact-title { font-size: 11px; font-weight: 300; margin-top: 3px; opacity: 0.9; }
  .contact-list { list-style: none; margin-top: 12px; font-size: 13px; font-weight: 300; }
  .contact-list li { display: flex; align-items: center; gap: 8px; margin-bottom: 5px; }
  .contact-list svg { width: 12px; height: 12px; fill: none; stroke: var(--white); stroke-width: 1.6; }
  .address {
    position: absolute;
    bottom: 20px;
    left: 34px;
    font-size: 14px;
    color: var(--ink);
  }
</style>
</head>
<body>
  <section class="card card--front" aria-label="Card front">
    <div class="front-brand">
      <div class="brand-dot"></div>
      <div class="brand-name">Meriden Therapeutics</div>
    </div>
    <p class="front-web">www.<span>meridenrx</span>.com</p>
  </section>

  <section class="card card--back" aria-label="Card back">
    <div class="back-brand">Meriden Therapeutics</div>
    <div class="band"></div>
    <div class="band-mark"></div>
    <div class="contact">
      <h1 class="contact-name">Daniel Whitford</h1>
      <p class="contact-title">Senior Director of Marketing</p>
      <ul class="contact-list">
        <li>
          <svg viewBox="0 0 12 12"><path d="M2 1h2.5l1 2.5-1.5 1a6 6 0 0 0 3.5 3.5l1-1.5 2.5 1V11A9 9 0 0 1 1 2z"/></svg>
          555-210-4417
        </li>
        <li>
          <svg viewBox="0 0 12 12"><rect x="3" y="1" width="6" height="10" rx="1"/><line x1="5" y1="9" x2="7" y2="9"/></svg>
          555-318-6620
        </li>
        <li>
          <svg viewBox="0 0 12 12"><circle cx="6" cy="6" r="5"/><ellipse cx="6" cy="6" rx="2.2" ry="5"/><line x1="1" y1="6" x2="11" y2="6"/></svg>
          dwhitford@meridenrx.com
        </li>
      </ul>
    </div>
    <p class="address">118 Harbor Lane Fairview, GA 30012</p>
  </section>
</body>
</html>
```